Harborline Benches business cards

I’d like a business card design that includes my logo, a tag line and my contact info. Black, textured background. My contact info color should match the orange and blue gradients. Tagline under logo: “Wooden Tables and Furniture of the Highest Quality”

Target Market(s)

High end furniture buyers

Contact Information for Business Card

Contact info, logo and tagline

```html
<!DOCTYPE html>
<html lang="en">
<head>
<meta charset="utf-8">
<title>Harborline Benches – Business Cards</title>
<link rel="stylesheet" href="https://fonts.googleapis.com/css2?family=Poppins:wght@400;500;600;700&display=swap">
<style>
  :root {
    --stage: #3a3a3c;
    --card-black: #161618;
    --card-silver: #6e6e70;
    --card-grey: #2e2e30;
    --paper: #ffffff;
    --orange: #ee7424;
    --orange-soft: #f6b07c;
    --blue: #0a4fa8;
    --ink: #3a3a3a;
    --rule: #c4c4c4;
  }
  * { box-sizing: border-box; margin: 0; padding: 0; }
  html, body { width: 1200px; height: 689px; overflow: hidden; }
  body {
    background: var(--stage);
    font-family: "Poppins", sans-serif;
    position: relative;
  }
  .card {
    position: absolute;
    top: 190px;
    width: 540px;
    height: 309px;
    border-radius: 18px;
    overflow: hidden;
    box-shadow: 0 18px 40px rgba(0,0,0,.45);
  }

  /* Back side */
  .card-back { left: 30px; background: var(--card-black); }
  .tree-pattern {
    position: absolute; inset: 0;
    background: linear-gradient(215deg, var(--card-silver) 0%, #4a4a4c 18%, var(--card-grey) 45%, var(--card-black) 80%);
  }
  .back-name {
    position: absolute; left: 0; right: 0; top: 134px;
    text-align: center;
    font-size: 32px; font-weight: 500;
    color: var(--orange);
    letter-spacing: .3px;
  }

  /* Front side */
  .card-front { left: 630px; background: var(--paper); }
  .front-brand {
    position: absolute; left: 28px; top: 150px;
    font-size: 21px; font-weight: 500;
    color: var(--blue);
    white-space: nowrap;
  }
  .divider {
    position: absolute; left: 262px; top: 50px;
    width: 1px; height: 170px; background: var(--rule);
  }
  .details { position: absolute; left: 284px; top: 44px; width: 240px; }
  .person-name { font-size: 27px; font-weight: 700; line-height: 1.1; }
  .person-name .first { color: var(--orange); }
  .person-name .last { color: var(--blue); }
  .person-role { font-size: 13px; color: var(--ink); margin-bottom: 14px; }
  .contact-list { list-style: none; font-size: 12.5px; color: var(--ink); line-height: 1.45; }
  .contact-list li { display: flex; align-items: flex-start; gap: 7px; }
  .contact-list svg { width: 11px; height: 11px; margin-top: 4px; flex: none; }
  .contact-list .address { margin-top: 10px; }
  .tree-art {
    position: absolute; right: 40px; bottom: 62px;
    width: 60px; height: 80px;
    background: linear-gradient(180deg, var(--orange-soft) 0%, var(--orange) 100%);
    border-radius: 30px 30px 4px 4px;
    opacity: .8;
  }
  .tagline-band {
    position: absolute; left: 0; right: 46px; bottom: 0; height: 44px;
    background: var(--orange);
    color: var(--paper);
    font-size: 15px; font-weight: 600;
    display: flex; align-items: center; justify-content: center;
    letter-spacing: .3px;
  }
  .corner-block {
    position: absolute; right: 0; bottom: 0; width: 46px; height: 62px;
    background: var(--blue);
  }
</style>
</head>
<body>
  <section class="card card-back">
    <div class="tree-pattern" role="img" aria-label="Textured repeating pattern of silver bare trees fading into black"></div>
    <div class="back-name">Harborline Benches</div>
  </section>

  <section class="card card-front">
    <div class="front-brand">Harborline Benches</div>
    <div class="divider"></div>
    <div class="details">
      <p class="person-name"><span class="first">Marcus</span> <span class="last">Ellery</span></p>
      <p class="person-role">Managing Director</p>
      <ul class="contact-list">
        <li><svg viewBox="0 0 12 12"><path fill="var(--orange)" d="M2.5 1 L4.5 1 L5.2 3.6 L4 4.6 Q5 6.8 7.4 8 L8.4 6.8 L11 7.5 L11 9.5 Q10.5 11 9 11 Q1 10 1 2.5 Q1 1 2.5 1Z"/></svg>055-210 384 617</li>
        <li><svg viewBox="0 0 12 12"><rect x="0.5" y="2" width="11" height="8" rx="1" fill="var(--orange)"/><path d="M1 2.5 L6 6.5 L11 2.5" stroke="#fff" fill="none"/></svg>hello@harborline.com</li>
        <li><svg viewBox="0 0 12 12"><circle cx="6" cy="6" r="5" fill="none" stroke="var(--orange)" stroke-width="1.3"/><path d="M1 6 H11 M6 1 Q3 6 6 11 Q9 6 6 1" fill="none" stroke="var(--orange)"/></svg>www.harborline.com</li>
        <li class="address"><svg viewBox="0 0 12 12"><path fill="var(--orange)" d="M6 0.5 A4 4 0 0 1 10 4.5 Q10 7 6 11.5 Q2 7 2 4.5 A4 4 0 0 1 6 0.5Z"/><circle cx="6" cy="4.5" r="1.5" fill="#fff"/></svg><span>48, Quay Lane<br>Harbor City, 204815</span></li>
      </ul>
    </div>
    <div class="tree-art" role="img" aria-label="Orange bare tree illustration"></div>
    <div class="tagline-band">Wooden Tables and Furniture of the Highest Quality</div>
    <div class="corner-block"></div>
  </section>
</body>
</html>
```